Quillmere Supply Chain and Logistic Consulting

Please review the attached Business Card. I want as close to this card with the colors, fonts, and quality of the card as possible. The attached compass should replace the deer head on both sides of the card and the text should say:

Backside
Compass JPEG
Quillmere SC&L
A Supply Chain and Logistics Consulting Company

Frontside
Quillmere SC&L
Ray Falkner - Tampa Florida
President
____________________________________
(555) 314-9027
QuillmereSCL@Examplemail.com
_____________________________________

Bottom Front Side

Target Market(s)

Businesses

Contact Information for Business Card

Backside
Compass JPEG
Quillmere SC&L

Frontside
Quillmere SC&L
President
(555) 314-9027
QuillmereSCL@Examplemail.com

Bottom Front Side

Font styles to use
Serif
Script

Colors

Designer to choose colors to be used in the design.

Requirements
Must have
• See attached card for reference
Nice to have
Should not have

```html
<!DOCTYPE html>
<html lang="en">
<head>
<meta charset="utf-8">
<title>Quillmere SC&amp;L – Business Card</title>
<link rel="stylesheet" href="https://fonts.googleapis.com/css2?family=Cinzel:wght@400&family=Tinos&display=swap">
<style>
  :root {
    --backdrop: #4b4c4c;
    --card: #1f1f1f;
    --card-edge: #262626;
    --ink: #f2f2f2;
    --ink-soft: #c8c8c8;
    --rule: #8a8a8a;
    --mark: #bdbdbd;
  }
  * { margin: 0; padding: 0; box-sizing: border-box; }
  html, body {
    width: 963px; height: 1200px; overflow: hidden;
    background: var(--backdrop);
  }
  .canvas { position: relative; width: 963px; height: 1200px; }
  .card {
    position: absolute; left: 232px; width: 556px; height: 317px;
    background: linear-gradient(135deg, var(--card-edge), var(--card) 60%);
    color: var(--ink);
    font-family: "Tinos", "Times New Roman", serif;
  }
  .card--front { top: 221px; }
  .card--back { top: 636px; }

  .brand-name {
    font-family: "Tinos", "Times New Roman", serif;
    font-size: 26px; font-weight: 400; line-height: 1;
  }
  .brand-tagline {
    font-size: 10px; margin-top: 5px; color: var(--ink-soft);
  }

  .front__brand { position: absolute; left: 30px; top: 60px; }
  .front__rule {
    position: absolute; left: 31px; top: 130px; width: 72px; height: 1px;
    background: linear-gradient(90deg, var(--rule), transparent);
  }
  .person { position: absolute; left: 30px; top: 166px; font-family: "Cinzel", "Times New Roman", serif; }
  .person__name { font-size: 22px; letter-spacing: 1px; line-height: 1; }
  .person__title { font-size: 15px; letter-spacing: 1px; margin-top: 3px; }
  .contacts { position: absolute; left: 31px; top: 223px; list-style: none; }
  .contacts li {
    display: flex; align-items: center; gap: 8px;
    font-size: 13.5px; height: 18px; color: var(--ink);
  }
  .contacts svg { width: 11px; height: 11px; fill: var(--ink); flex: none; }

  .back__mark {
    position: absolute; left: 50%; top: 73px; width: 112px; height: 112px;
    margin-left: -56px; border: 2px solid var(--mark); border-radius: 50%;
  }
  .back__brand { position: absolute; left: 0; right: 0; top: 207px; text-align: center; }
</style>
</head>
<body>
<main class="canvas">
  <section class="card card--front" aria-label="Card front">
    <div class="front__brand">
      <p class="brand-name">Quillmere SC&amp;L</p>
      <p class="brand-tagline">A Supply Chain and Logistics Consulting Company</p>
    </div>
    <div class="front__rule"></div>
    <div class="person">
      <p class="person__name">Ray Falkner</p>
      <p class="person__title">President</p>
    </div>
    <ul class="contacts">
      <li>
        <svg viewBox="0 0 12 12" aria-hidden="true"><path d="M2.4 0.6 4.3 2.8 3.3 4.2c.8 1.7 2.2 3.1 3.9 3.9l1.4-1 2.2 1.9-1.3 2.3C5 11 1 7 .6 2z"/></svg>
        (555) 314-9027
      </li>
      <li>
        <svg viewBox="0 0 12 12" aria-hidden="true"><path d="M0 2.5h12v7H0z M.8 3.2 6 7l5.2-3.8" fill="none" stroke="#f2f2f2" stroke-width="1.2"/></svg>
        QuillmereSCL@Examplemail.com
      </li>
      <li>
        <svg viewBox="0 0 12 12" aria-hidden="true"><circle cx="6" cy="6" r="5.3" fill="none" stroke="#f2f2f2" stroke-width="1.2"/><path d="M2.5 3.5c1.5 0 2 1 1.5 2S5 7 5 8.5L6.5 10c1-1 1.5-2 .5-3S5.5 5 6.5 4 8 2 7 1.2C5 1 3.5 2 2.5 3.5z"/></svg>
        www.quillmerescl.example
      </li>
    </ul>
  </section>

  <section class="card card--back" aria-label="Card back">
    <div class="back__mark" aria-hidden="true"></div>
    <div class="back__brand">
      <p class="brand-name">Quillmere SC&amp;L</p>
      <p class="brand-tagline">A Supply Chain and Logistics Consulting Company</p>
    </div>
  </section>
</main>
</body>
</html>
```